Personal training and nutrition business needs business card design

We need a business card that outlays our services and invites potential customers to join our team and take the first step to a healthier and more enjoyable life. We cater for any level of fitness and specialize in weight loss and conditioning, strength training, muscle gain and strength endurance. Whether you are just starting off or need some help getting to the next level of your journey we are here to get the job done.
We specialize in one on one or one on two personal training sessions and each program will be custom made to suit individual fitness goals of our clients

```html
<!DOCTYPE html>
<html lang="en">
<head>
<meta charset="utf-8">
<title>Stride &amp; Form business card</title>
<link href="https://fonts.googleapis.com/css2?family=Arimo:wght@400;700&display=swap" rel="stylesheet">
<style>
  :root {
    --stage: #1c1c1e;
    --card-light: #ffffff;
    --card-dark: #2b2b2d;
    --ink: #1a1a1a;
    --ink-soft: #3a3a3a;
    --purple: #8e4fbf;
    --purple-deep: #6a3fb2;
    --purple-pink: #b25fb8;
    --grey-fade: #6a6a6d;
  }
  * { box-sizing: border-box; margin: 0; padding: 0; }
  html, body { width: 1200px; height: 900px; overflow: hidden; }
  body {
    background: var(--stage);
    font-family: "Arimo", Arial, sans-serif;
    display: flex;
    align-items: center;
    justify-content: center;
    gap: 60px;
  }
  .card {
    position: relative;
    width: 500px;
    height: 286px;
    border-bottom: 4px solid var(--purple);
    box-shadow: 0 14px 30px rgba(0,0,0,.5);
    overflow: hidden;
  }
  .card--front { background: var(--card-light); color: var(--ink); }
  .card--back {
    background: radial-gradient(ellipse at 35% 30%, var(--grey-fade) 0%, var(--card-dark) 60%);
  }

  .brand { position: absolute; left: 34px; top: 30px; display: flex; align-items: center; gap: 10px; }
  .brand__mark { width: 22px; height: 22px; background: var(--purple); }
  .brand__name { font-weight: 700; font-size: 26px; letter-spacing: 1px; text-transform: uppercase; color: var(--ink); }
  .brand__tagline {
    position: absolute; left: 34px; top: 68px;
    font-size: 8px; letter-spacing: 1.2px; text-transform: uppercase; color: var(--purple);
  }

  .contact { position: absolute; left: 34px; top: 104px; list-style: none; font-size: 13px; color: var(--ink-soft); }
  .contact li { display: flex; align-items: center; gap: 8px; margin-bottom: 6px; }
  .contact svg { width: 12px; height: 12px; flex: none; }
  .slogan { position: absolute; left: 34px; top: 182px; font-size: 13px; color: var(--ink-soft); }

  .person { position: absolute; right: 34px; top: 104px; text-align: right; }
  .person__name { font-weight: 700; font-size: 18px; letter-spacing: 1px; color: var(--purple-deep); text-transform: uppercase; }
  .person__role { font-size: 13px; color: var(--ink-soft); margin-top: 3px; }
  .person__address { font-size: 13px; color: var(--ink-soft); margin-top: 14px; line-height: 1.4; }

  .motto { position: absolute; left: 0; right: 0; bottom: 22px; text-align: center; font-size: 13px; color: var(--ink-soft); }

  .back__brand { position: absolute; right: 34px; bottom: 40px; text-align: right; }
  .back__name { font-weight: 700; font-size: 30px; letter-spacing: 1.5px; color: #ffffff; text-transform: uppercase; }
  .back__tagline { font-size: 8px; letter-spacing: 1.2px; text-transform: uppercase; color: var(--purple-pink); margin-top: 6px; }
</style>
</head>
<body>
  <section class="card card--front">
    <div class="brand">
      <span class="brand__mark"></span>
      <span class="brand__name">Stride &amp; Form</span>
    </div>
    <p class="brand__tagline">Personal training. Nutrition. Motivation</p>

    <ul class="contact">
      <li>
        <svg viewBox="0 0 12 12"><path d="M3 1 L5 3.5 L4 5 Q5.5 7 7 8 L8.5 7 L11 9 L9.5 11 Q4 10 1 2.5 Z" fill="var(--purple)"/></svg>
        555-014-2100
      </li>
      <li>
        <svg viewBox="0 0 12 12"><rect x="1" y="2.5" width="10" height="7" fill="none" stroke="var(--purple)"/><path d="M1 2.5 L6 6.5 L11 2.5" fill="none" stroke="var(--purple)"/></svg>
        hello@strideform.com
      </li>
      <li>
        <svg viewBox="0 0 12 12"><circle cx="6" cy="6" r="5" fill="none" stroke="var(--purple)"/><ellipse cx="6" cy="6" rx="2.2" ry="5" fill="none" stroke="var(--purple)"/><path d="M1 6 H11" stroke="var(--purple)"/></svg>
        www.strideform.com
      </li>
    </ul>
    <p class="slogan">Strong body, Strong mind</p>

    <div class="person">
      <h1 class="person__name">Marcus Hale</h1>
      <p class="person__role">Manager</p>
      <p class="person__address">Your address<br>city, state, ZIP 0000</p>
    </div>

    <p class="motto">commit Preform succeed</p>
  </section>

  <section class="card card--back">
    <div class="back__brand">
      <p class="back__name">Stride &amp; Form</p>
      <p class="back__tagline">Personal training. Nutrition. Motivation</p>
    </div>
  </section>
</body>
</html>
```